Business Card Design

I'm looking for a cool business card design that showcases what my company does... I am the owner and Corvane is a play on my last name. The Corvane Group is a privately held entity that specializes in media (Corvane Media) and financial services (Corvane Trading).

Corvane Media focuses on the distribution and management of quality entertainment properties to all areas of the media world including broadcast, cable, digital, mobile and social media. Corvane Media helps media and entertainment companies create and market great content and ensure that it reaches the widest audience possible.

Corvane Media currently represents Tilda TV (www.tildatv-example.com), the fastest growing over the air broadcast network that focuses on programming that appeals to the African American audience. Corvane Media also represents two new over the air broadcast networks launching in Summer 2014 - Harbor TV (www.harbortv-example.com) and Plume TV (www.plumetv-example.com).

Corvane Media is an investor and business partner in DriftLoom (www.driftloom-example.com) - a mobile social platform that empowers the user to choose how long your photos and videos live online.

Corvane Media also represents RKM Enterprises (www.rkment-example.com), an independent producer that creates talent-driven and cost-effective programming around emerging talent and Solvering Content, a prolific producer of multimedia content including QNR's hit program - Pellet Q.

Corvane Trading manages a family office and focuses on building meaningful partnerships with all major financial institutions with a heavy concentration on IPO and secondary offerings.

Industry/Entity Type

Entertainment

Contact Information for Business Card

Dennis Harrow
12 Quillan Court
Roslyn New York 11592
O 516.555.0143
C 516.555.0187

```html
<!DOCTYPE html>
<html lang="en">
<head>
<meta charset="utf-8">
<title>The Corvane Group – Business Card</title>
<link rel="stylesheet" href="https://fonts.googleapis.com/css2?family=Open+Sans:wght@400;600;700&display=swap">
<style>
  :root {
    --backdrop: #3b3b3b;
    --card: #ffffff;
    --orange: #e07f26;
    --taupe: #767069;
    --brand-text: #6f6a64;
    --moon: #efe7cc;
    --contact-text: #ffffff;
  }
  * { margin: 0; padding: 0; box-sizing: border-box; }
  html, body {
    width: 1200px;
    height: 900px;
    overflow: hidden;
    background: var(--backdrop);
  }
  .canvas {
    position: relative;
    width: 1200px;
    height: 900px;
  }
  .card {
    position: absolute;
    left: 100px;
    top: 165px;
    width: 1000px;
    height: 571px;
    background: var(--card);
    overflow: hidden;
    font-family: "Open Sans", sans-serif;
  }
  .card__swoosh {
    position: absolute;
    inset: 0;
    width: 100%;
    height: 100%;
  }
  .swoosh--taupe { fill: var(--taupe); }
  .swoosh--orange { fill: var(--orange); }

  .holder-name {
    position: absolute;
    top: 44px;
    right: 48px;
    font-size: 38px;
    color: var(--orange);
    font-weight: 400;
    letter-spacing: 0.2px;
  }
  .holder-name__last { font-weight: 700; }

  .brand {
    position: absolute;
    left: 70px;
    top: 150px;
    display: flex;
    align-items: center;
    gap: 26px;
  }
  .brand__disc {
    width: 150px;
    height: 150px;
    border-radius: 50%;
    background: var(--moon);
    flex: none;
  }
  .brand__name {
    font-size: 54px;
    line-height: 1.05;
    font-weight: 600;
    color: var(--brand-text);
    letter-spacing: 1px;
  }

  .contact {
    position: absolute;
    right: 40px;
    top: 384px;
    list-style: none;
    text-align: right;
    color: var(--contact-text);
    font-size: 24px;
    font-weight: 600;
    line-height: 37px;
  }
</style>
</head>
<body>
<main class="canvas">
  <section class="card" aria-label="Business card for The Corvane Group">
    <svg class="card__swoosh" viewBox="0 0 1000 571" preserveAspectRatio="none" aria-hidden="true">
      <path class="swoosh--taupe" d="M0,505 C360,470 760,330 1000,95 L1000,571 L0,571 Z"/>
      <path class="swoosh--orange" d="M0,538 C390,505 790,375 1000,165 L1000,571 L0,571 Z"/>
    </svg>

    <h1 class="holder-name">Dennis <span class="holder-name__last">Harrow</span></h1>

    <div class="brand">
      <div class="brand__disc"></div>
      <p class="brand__name">The Corvane<br>Group</p>
    </div>

    <ul class="contact">
      <li>516.555.0143 : O</li>
      <li>516.555.0187 : C</li>
      <li>12 Quillan Court Roslyn New York 11592 : A</li>
    </ul>
  </section>
</main>
</body>
</html>
```